High End Personalized Functional Medicine in Women's Health

We are adding new and exciting personalized medicine services to our Women's Health Care practice focusing on health optimization and anti-aging as well as hormone replacement therapy and need a high end brochure to educate patients about these services. We would like to see a zen-like design that has feminine appeal. Our office colors are vibrant but soothing. We have utilized the concepts of feng shui to optimize our positive energy. The exterior of the building is peach and cream and these colors would blend with that energy The final design should communicate a sense that you can take control of your health and aging.

Target Market(s)

Females age 35-65 with annual income >$75000/year

Industry/Entity Type

Health And Wellness

Logo Text

Bright Bloom is the company name. Our sister company is Cedar Mesa Ob/Gyn

Font styles to use
Serif

Colors

Designer to choose colors to be used in the design.

Requirements
Must have
• My project must have clean lines. I like a strong feminine appearance, not a fluffy curvy feminine look. Professional appearance, Brochure would be on thicker card stock. A strong front page that makes you want to open the brochure
Nice to have
• Eye catching photos that complement our message . I am not tied to the peach and cream color recommendation, but find those colors feminine but not so cliche as pinks and purples.
Should not have
• frilly design

```html
<!DOCTYPE html>
<html lang="en">
<head>
<meta charset="utf-8">
<title>Bright Bloom Functional Medicine – Trifold Brochure</title>
<link href="https://fonts.googleapis.com/css2?family=Open+Sans:wght@300;400;600&display=swap" rel="stylesheet">
<style>
:root{
  --bg-top:#9a9ea2;
  --bg-bottom:#7d8185;
  --paper:#ffffff;
  --cream:#f7f1ee;
  --blush:#e6cdc6;
  --rose:#d5aea5;
  --rose-deep:#c3958b;
  --rose-text:#b98379;
  --ink:#5e5757;
  --ink-soft:#7c7373;
  --photo-sand:#c9ad92;
  --photo-sky:#e9dcd0;
  --photo-dusk:#b89a8a;
}
*{box-sizing:border-box;margin:0;padding:0}
html,body{width:1200px;height:2400px;overflow:hidden}
body{
  background:linear-gradient(180deg,var(--bg-top),var(--bg-bottom));
  font-family:"Open Sans",Arial,sans-serif;
  color:var(--ink);
  position:relative;
}
.spread{
  position:absolute;left:30px;width:1140px;height:880px;
  display:flex;box-shadow:0 18px 40px rgba(0,0,0,.28);
}
.spread--outside{top:200px}
.spread--inside{top:1300px}
.panel{
  position:relative;width:380px;height:880px;background:var(--paper);
  display:flex;flex-direction:column;overflow:hidden;
}
.panel + .panel{border-left:1px solid rgba(0,0,0,.06)}
.panel--rose{background:var(--blush)}
.photo{width:100%;flex:none}
.photo--lake{height:330px;background:linear-gradient(180deg,#eadfd3 0%,#d9c3b0 45%,#a99584 70%,#8d7c6c 100%)}
.photo--beach{height:300px;background:linear-gradient(160deg,#efe4d8 0%,#d8c0a6 50%,#b99d82 100%);position:relative}
.photo--walk{height:430px;background:linear-gradient(180deg,#efe6dc 0%,#dcc7b2 40%,#b89878 75%,#8f735c 100%)}
.photo--couple{height:250px;background:linear-gradient(135deg,#e8eef2 0%,#cfd7de 50%,#a9b2bb 100%);margin-top:auto}
.photo-round{
  width:150px;height:150px;border-radius:50%;border:5px solid var(--paper);
  background:linear-gradient(135deg,#a6b6c3,#c9b3a5 60%,#8e9a7c);
  margin:40px auto 0;flex:none;
}
.photo-inset{
  position:absolute;right:26px;bottom:-40px;width:110px;height:110px;border-radius:50%;
  border:4px solid var(--paper);background:linear-gradient(135deg,#9c7a68,#d4b9a6);
}
.body{padding:26px 30px 0;font-size:13px;line-height:1.65;color:var(--ink-soft)}
.body p + p{margin-top:12px}
.heading{
  font-size:19px;font-weight:400;line-height:1.3;color:var(--rose-text);
  padding-bottom:10px;border-bottom:1px solid var(--rose);margin:22px 0 12px;
}
.panel--rose .heading{color:var(--ink)}
.band{
  margin-top:auto;height:56px;background:var(--rose);color:var(--paper);
  display:flex;align-items:center;justify-content:center;gap:10px;
  font-size:15px;letter-spacing:.04em;flex:none;
}
.band svg{width:18px;height:18px}
/* cover */
.brand{text-align:center;padding-top:46px;flex:none}
.brand-dot{width:46px;height:46px;border-radius:50%;border:1.5px solid var(--rose-deep);margin:0 auto 14px}
.brand-name{font-size:22px;font-weight:300;letter-spacing:.42em;color:var(--rose-text);text-transform:uppercase}
.brand-sub{font-size:14px;font-weight:300;letter-spacing:.14em;color:var(--rose-text);text-transform:uppercase;margin-top:6px}
.cover .photo--walk{margin-top:30px}
.cover-title{
  font-size:23px;font-weight:400;line-height:1.35;color:var(--ink);
  padding:28px 30px 0;
}
/* testimonials */
.testimonials{text-align:center;padding:0 32px}
.testimonials .heading{border:none;text-align:center;font-size:18px}
.quote-mark{font-size:44px;line-height:1;color:var(--rose-deep);font-weight:600;margin-top:6px}
.quote{font-size:13px;font-style:italic;line-height:1.6;color:var(--ink-soft)}
.contact{text-align:center;font-size:13px;line-height:1.7;color:var(--ink);margin-top:26px}
.social{display:flex;justify-content:center;gap:12px;margin-top:14px}
.social span{width:26px;height:26px;border-radius:50%;background:var(--rose-deep)}
/* symptoms */
.symptoms{padding:0 30px}
.symptoms .heading{color:var(--paper);border-color:rgba(255,255,255,.6)}
.symptom{display:flex;gap:14px;margin-top:18px}
.symptom-icon{flex:none;width:34px;height:34px;border-radius:50%;border:1.5px solid var(--paper)}
.symptom h3{font-size:14px;font-weight:600;letter-spacing:.08em;color:var(--paper);text-transform:uppercase}
.symptom p{font-size:13px;line-height:1.55;color:#fff8f5;margin-top:3px}
.panel--symptoms{background:var(--rose)}
.panel--symptoms .band{background:var(--rose-deep)}
</style>
</head>
<body>

<section class="spread spread--outside" aria-label="Brochure outside">
  <article class="panel">
    <div class="photo photo--lake" role="img" aria-label="Photo of a woman meditating on a lakeside dock at sunrise"></div>
    <div class="body">
      <p>Functional medicine's aim is to treat the whole person and to bring balance to the body, mind and spirit so you can feel your best at every age.</p>
      <p>Dr. Elena Rowan is a board certified gynecologist who has cared for women at Cedar Mesa Ob/Gyn for over fifteen years.</p>
      <p>She recently completed advanced training in functional and integrative medicine to offer a deeper, more personal plan for each patient she sees.</p>
    </div>
    <div class="band">www.brightbloomhealth.com</div>
  </article>

  <article class="panel panel--rose">
    <div class="photo-round" role="img" aria-label="Round photo of a group of smiling women sitting together outdoors"></div>
    <div class="testimonials">
      <h2 class="heading">What do patients have to say about their experience with Dr. Rowan</h2>
      <div class="quote-mark">&ldquo;</div>
      <p class="quote">Dr. Rowan provides professional and caring service. I always leave her office feeling heard, hopeful and in control of my health. – Sarah</p>
      <div class="quote-mark">&ldquo;</div>
      <p class="quote">The staff at Cedar Mesa Ob/Gyn are all very kind and supportive. I would recommend Dr. Rowan to all of my friends and family. – Maria</p>
      <div class="contact">
        Bright Bloom Functional Medicine<br>
        212 Juniper Lane, Cedar Mesa, NM<br>
        Phone: 505-555-0148<br>
        hello@brightbloomhealth.com
      </div>
      <div class="social" aria-hidden="true"><span></span><span></span><span></span></div>
    </div>
    <div class="band" style="background:var(--rose-deep)">
      <svg viewBox="0 0 24 24" fill="none" stroke="currentColor" stroke-width="2"><path d="M5 3h4l2 5-3 2a12 12 0 0 0 6 6l2-3 5 2v4a2 2 0 0 1-2 2A17 17 0 0 1 3 5a2 2 0 0 1 2-2z"/></svg>
      505-555-0148
    </div>
  </article>

  <article class="panel cover">
    <div class="brand">
      <div class="brand-dot"></div>
      <div class="brand-name">Bright Bloom</div>
      <div class="brand-sub">Functional Medicine</div>
    </div>
    <div class="photo photo--walk" role="img" aria-label="Photo of three women walking arm in arm along a beach at sunset"></div>
    <h1 class="cover-title">High End Personalized Functional Medicine in Women's Health</h1>
    <div class="band">www.brightbloomhealth.com</div>
  </article>
</section>

<section class="spread spread--inside" aria-label="Brochure inside">
  <article class="panel">
    <div class="photo photo--beach" role="img" aria-label="Photo of a woman in a sun hat sitting on the sand by the sea">
      <div class="photo-inset" role="img" aria-label="Round photo of a hands-on wellness treatment"></div>
    </div>
    <div class="body">
      <h2 class="heading">Why should you consider a functional medicine visit?</h2>
      <p>You are tired of feeling tired. You can't lose weight, you can't sleep, and you worry about the future. You want answers and a plan that fits your life, not a quick fix.</p>
      <h2 class="heading">Who else should consider a functional medicine visit?</h2>
      <p>You want to achieve optimal health with a personalized approach. You are ready to take a proactive role in aging well and reaching the highest level of health you can achieve.</p>
    </div>
    <div class="band">www.brightbloomhealth.com</div>
  </article>

  <article class="panel panel--symptoms">
    <div class="symptoms">
      <h2 class="heading" style="margin-top:34px">What Symptoms Do We Treat?</h2>
      <div class="symptom"><span class="symptom-icon"></span><div><h3>Weight Gain</h3><p>Stubborn weight that will not move despite diet and exercise, often linked to hormones.</p></div></div>
      <div class="symptom"><span class="symptom-icon"></span><div><h3>Fatigue</h3><p>Low energy, poor sleep and brain fog that keep you from living fully.</p></div></div>
      <div class="symptom"><span class="symptom-icon"></span><div><h3>Depression</h3><p>Mood swings, anxiety and low mood that can follow shifts in body chemistry.</p></div></div>
      <div class="symptom"><span class="symptom-icon"></span><div><h3>Female Hormone Imbalance</h3><p>Irregular cycles, hot flashes and night sweats treated with a careful, tailored plan.</p></div></div>
      <div class="symptom"><span class="symptom-icon"></span><div><h3>Low Libido</h3><p>Loss of desire and comfort that can be restored with the right support.</p></div></div>
    </div>
    <div class="band">
      <svg viewBox="0 0 24 24" fill="none" stroke="currentColor" stroke-width="2"><path d="M5 3h4l2 5-3 2a12 12 0 0 0 6 6l2-3 5 2v4a2 2 0 0 1-2 2A17 17 0 0 1 3 5a2 2 0 0 1 2-2z"/></svg>
      505-555-0148
    </div>
  </article>

  <article class="panel">
    <div class="body">
      <h2 class="heading" style="margin-top:34px">What can I expect from my first visit?</h2>
      <p>Your first visit is a longer appointment where we review your full history, lifestyle and goals. We order detailed lab testing and build a plan that is yours alone.</p>
      <h2 class="heading">What are your treatment protocols based on?</h2>
      <p>Our protocols are based on current research in hormone health, nutrition and metabolism. We use bioidentical hormones, targeted supplements and lifestyle changes to restore balance and energy.</p>
    </div>
    <div class="photo photo--couple" role="img" aria-label="Photo of a smiling mature couple relaxing together at home"></div>
  </article>
</section>

</body>
</html>
```